HearthMile business card and stationary design

We are looking for a simple yet elegant design for our mortgage company business card and stationary.

The card should include:
Name (Marcus Pell)
Title (CEO)
Phone Number (732-555-0182)
Address (48 Birchwell Court, Suite 314, Fernhollow, EX 00942)
Email (email@hearthmile.example)
"NMLS" i.e. (NMLS 61947)
"Company NMLS" (Company NMLS 274615)

Contact Information for Business Card

See above

```html
<!DOCTYPE html>
<html lang="en">
<head>
<meta charset="utf-8">
<title>HearthMile Business Card</title>
<link rel="stylesheet" href="https://fonts.googleapis.com/css2?family=Montserrat:wght@600;700&family=Roboto:wght@400&display=swap">
<style>
  :root {
    --stage: #d9dadb;
    --card: #14202d;
    --accent: #1a9de0;
    --text: #ffffff;
    --rule: #8a939c;
  }
  * { box-sizing: border-box; margin: 0; padding: 0; }
  html, body { width: 1200px; height: 800px; overflow: hidden; }
  body {
    background: var(--stage);
    position: relative;
    font-family: "Roboto", Arial, sans-serif;
  }
  .card {
    position: absolute;
    top: 240px;
    width: 560px;
    height: 320px;
    background: var(--card);
    border-radius: 22px;
    border-bottom: 4px solid var(--accent);
    color: var(--text);
    overflow: hidden;
  }
  .card--front { left: 30px; }
  .card--back { left: 610px; }

  .brand {
    font-family: "Montserrat", Arial, sans-serif;
    font-weight: 700;
    color: var(--accent);
    letter-spacing: 0.5px;
    line-height: 1;
    white-space: nowrap;
  }
  .card--front .brand {
    position: absolute;
    top: 62px;
    right: 120px;
    font-size: 38px;
  }
  .card--back .brand {
    position: absolute;
    top: 50%;
    left: 50%;
    transform: translate(-50%, -50%);
    font-size: 64px;
  }

  .person {
    position: absolute;
    left: 40px;
    top: 138px;
  }
  .person__name {
    font-family: "Montserrat", Arial, sans-serif;
    font-weight: 700;
    font-size: 22px;
    line-height: 26px;
  }
  .person__title {
    color: var(--accent);
    font-size: 15px;
    line-height: 18px;
    margin-top: 2px;
  }

  .divider {
    position: absolute;
    left: 40px;
    right: 40px;
    top: 196px;
    height: 1px;
    background: var(--rule);
  }

  .contact {
    position: absolute;
    left: 40px;
    top: 212px;
    list-style: none;
    font-size: 16px;
    line-height: 24px;
    white-space: nowrap;
  }
  .contact li { display: flex; align-items: center; gap: 10px; }
  .contact svg { width: 12px; height: 12px; fill: var(--accent); flex: none; }

  .office {
    position: absolute;
    right: 40px;
    top: 212px;
    text-align: right;
    font-size: 15px;
    line-height: 22px;
    font-style: normal;
    white-space: nowrap;
  }
</style>
</head>
<body>
  <section class="card card--front" aria-label="Business card, contact side">
    <div class="brand">HearthMile</div>

    <div class="person">
      <div class="person__name">Marcus Pell</div>
      <div class="person__title">CEO</div>
    </div>

    <div class="divider"></div>

    <ul class="contact">
      <li>
        <svg viewBox="0 0 12 12" aria-hidden="true"><path d="M2.5 0.5 L4.5 0.5 L5 3.5 L3.6 4.4 C4.3 6 5.9 7.6 7.6 8.4 L8.5 7 L11.5 7.5 L11.5 9.5 C11.5 10.6 10.6 11.5 9.5 11.5 C4.5 11.2 0.8 7.5 0.5 2.5 C0.5 1.4 1.4 0.5 2.5 0.5 Z"/></svg>
        <span>732-555-0182</span>
      </li>
      <li>
        <svg viewBox="0 0 12 12" aria-hidden="true"><path d="M0 2 H12 V10 H0 Z M0.8 2.6 L6 6.6 L11.2 2.6 V3.6 L6 7.6 L0.8 3.6 Z" fill-rule="evenodd"/></svg>
        <span>info@hearthmile.example</span>
      </li>
      <li>
        <svg viewBox="0 0 12 12" aria-hidden="true"><circle cx="6" cy="6" r="5.5" fill="none" stroke="#1a9de0" stroke-width="1.2"/><ellipse cx="6" cy="6" rx="2.3" ry="5.5" fill="none" stroke="#1a9de0" stroke-width="1"/><path d="M0.5 6 H11.5" stroke="#1a9de0" stroke-width="1"/></svg>
        <span>hearthmile.example</span>
      </li>
    </ul>

    <address class="office">
      48 Birchwell Court, Suite 314<br>
      Fernhollow, EX 00942<br>
      NMLS 274615 | NMLS 61947
    </address>
  </section>

  <section class="card card--back" aria-label="Business card, brand side">
    <div class="brand">HearthMile</div>
  </section>
</body>
</html>
```